I need a sophisticated and powerful book cover design that combines Japanese minimalism with contemporary appeal. The cover should convey personal transformation through the metaphor of a katana (Japanese sword).
Key Design Elements:
A katana, either partially shown or artistically rendered
Subtle Japanese design elements without being stereotypical
Clean, minimalist aesthetic
Professional font selection that bridges Eastern and Western typography
Color scheme: Deep blacks, steel grays, and possibly a touch of red or gold for accent
Mood/Style:
Professional and sophisticated
Blend of traditional Japanese aesthetics with modern design
Should appeal to personal development and business readers
Must convey strength and transformation
Elegant rather than aggressive
Specific Requirements:
Title: "The Lantern Compass"
Subtitle: "Quiet Methods for Growing Inner Steadiness and Calm Endurance"
Author names: Dorvelan Thaske and Meloda Thaske
Cover dimensions: Standard hardcover book size (6" x 9")
Must work well in both physical and digital thumbnail formats
Should be striking and legible when viewed as a small image online
Design Specifics:
Japanese elements such as brushstroke effects, kanji characters, or wave patterns
The design should reflect the book's core message: personal transformation through Japanese wisdom principles, using the katana as a metaphor for growth and development.

```html
<!DOCTYPE html>
<html lang="en">
<head>
<meta charset="utf-8">
<title>The Lantern Compass — Book Cover</title>
<link href="https://fonts.googleapis.com/css2?family=Montserrat:wght@500;700&family=Shojumaru&display=swap" rel="stylesheet">
<style>
  :root {
    --page: #ffffff;
    --cover-ink: #15171c;
    --cover-deep: #101217;
    --ember: #f0642e;
    --ember-hot: #ffb15a;
    --steel: #5d7fb8;
    --steel-dark: #2a3550;
    --figure: #2b2a2c;
    --text: #ffffff;
  }
  * { margin: 0; padding: 0; box-sizing: border-box; }
  html, body {
    width: 1200px; height: 1200px; overflow: hidden;
    background: var(--page);
  }
  .cover {
    position: absolute;
    left: 240px; top: 60px;
    width: 720px; height: 1078px;
    background: var(--cover-ink);
    overflow: hidden;
    box-shadow: 2px 3px 6px rgba(0,0,0,0.25);
  }
  .cover-sky {
    position: absolute; inset: 0;
    background:
      radial-gradient(ellipse 200px 380px at 578px 230px, rgba(232, 84, 42, 0.30), transparent 72%),
      radial-gradient(ellipse 300px 420px at 580px 760px, rgba(60, 80, 110, 0.38), transparent 75%),
      linear-gradient(180deg, var(--cover-deep), var(--cover-ink) 60%, #1b1d22);
  }
  .figure-art {
    position: absolute;
    left: 470px; top: 690px;
    width: 250px; height: 388px;
    border-radius: 110px 110px 0 0;
    background: radial-gradient(ellipse at 50% 40%, #3a3634, var(--figure) 70%);
    opacity: 0.85;
  }
  .katana-art {
    position: absolute;
    left: 508px; top: 30px;
    width: 140px; height: 1000px;
    border-radius: 70px 70px 70px 70px / 90px 90px 160px 160px;
    background:
      linear-gradient(180deg,
        var(--ember-hot) 0%,
        var(--ember) 18%,
        #c0441f 52%,
        var(--steel) 62%,
        var(--steel-dark) 88%,
        rgba(42, 53, 80, 0.4) 100%);
    box-shadow: 0 0 40px rgba(240, 100, 46, 0.45);
  }
  .title {
    position: absolute; left: 47px; top: 50px;
    color: var(--text);
    line-height: 1;
    z-index: 2;
  }
  .title-line { display: block; }
  .title-top {
    font-family: "Montserrat", sans-serif; font-weight: 700;
    font-size: 84px; letter-spacing: 5px;
  }
  .title-brush {
    font-family: "Shojumaru", cursive;
    font-size: 72px; margin-top: 18px; letter-spacing: 0;
  }
  .title-bottom {
    font-family: "Montserrat", sans-serif; font-weight: 700;
    font-size: 94px; letter-spacing: 2px; margin-top: 18px;
  }
  .subtitle {
    position: absolute; left: 50px; top: 476px; width: 290px;
    font-family: "Montserrat", sans-serif; font-weight: 500;
    font-size: 29px; line-height: 38.5px; letter-spacing: 1px;
    color: var(--text);
    text-shadow: 0 2px 4px rgba(0,0,0,0.5);
    z-index: 2;
  }
  .authors {
    position: absolute; left: 50px; top: 955px;
    font-family: "Montserrat", sans-serif; font-weight: 500;
    font-size: 34px; line-height: 40px; letter-spacing: 2px;
    text-transform: uppercase;
    color: var(--text);
    z-index: 2;
  }
</style>
</head>
<body>
  <div class="cover">
    <div class="cover-sky"></div>
    <div class="figure-art" role="img" aria-label="Shadowed silhouette of a seated figure behind the blade"></div>
    <div class="katana-art" role="img" aria-label="Glowing katana standing point-down, hilt wrapped in swirling ember light, steel blade crackling with blue light, cherry blossoms drifting around it"></div>
    <h1 class="title">
      <span class="title-line title-top">THE</span>
      <span class="title-line title-brush">LANTERN</span>
      <span class="title-line title-bottom">COMPASS</span>
    </h1>
    <p class="subtitle">Quiet Methods for Growing Inner Steadiness and Calm Endurance</p>
    <p class="authors">Dorvelan Thaske<br>and Meloda Thaske</p>
  </div>
</body>
</html>
```